Personal Trainer website design

We are working with a personal trainer to design a website. They offer their primary services: Diet Coaching, In-Person Coaching (workouts), and Remote Coaching.
Some sites we like: https://www.mirabelthorne.com, https://kavialune.com/en-us, https://corvexfit.co.uk
Thank you for taking the time to consider designing a website for us. We are web developers based in Stockton, CA USA. Most of our projects go through the same process. Understanding this process may help you win a project with us. We custom-code all of our websites in-house. We don’t have any requirements as to what tools you use for your design, but ask that you follow these guidelines.
IMAGES:
We ask that if you use any images, or icons in the design, have a link to the asset, so we can purchase the image/icon. Most of the designs we submit do not have the customer’s images on them unless they have some great images. Be creative; show us the feeling that you are trying to portray with your image choices. Use any royalty-free site you choose. We subscribe to Quillon and mostly use their images, but are ok to purchase images outside of Quillon.
FONTS:
We ask that you identify the fonts you’re using in the design. This can be done in a message if you want. We typically use Brivane Fonts and Quillon Fonts.
CONTENT:
We're always open to different content and ideas. Often, we submit designs with stock images so that the client can see our vision. We typically go back and take pictures after the website launch to use their images with our vision. Lorem Ipsum is fine for paragraphs, but we ask that you make the Headers with correct English. We want to be able to show the vision and identify the sections of the website.
INSPIRATION:
We try and add a couple of links in the brief of some websites that we like to help you get started in your design.
REVISIONS:
We do not often ask for revisions of the designs unless we see something in the design that may not appeal to the client. If there are slight changes that we want to make, we simply do that in the development process.
FEEDBACK:
We rarely give feedback on designs during the design process. We are working on many website projects and do not have the time to give feedback. We usually respond if your request is well thought out and asks specific questions, but a note asking “feedback, please” usually goes unanswered.
1 page

```html
<!DOCTYPE html>
<html lang="en">
<head>
<meta charset="utf-8">
<title>Novafit – Personal Training</title>
<link href="https://fonts.googleapis.com/css2?family=Poppins:wght@400;500;600;700;800&display=swap" rel="stylesheet">
<style>
:root{
  --green:#869418;
  --green-dark:#6f7b12;
  --cream:#f4f6cc;
  --header:#d9d5cf;
  --ink:#1d1d1d;
  --text:#2a2a2a;
  --footer:#2b2b2b;
  --white:#ffffff;
}
*{margin:0;padding:0;box-sizing:border-box}
html,body{width:1200px;height:3027px;overflow:hidden}
body{position:relative;font-family:'Poppins',sans-serif;color:var(--text);background:var(--white)}
.abs{position:absolute}
.btn{position:absolute;display:flex;align-items:center;justify-content:center;border-radius:26px;background:var(--green);color:var(--white);font-size:17px;font-weight:400;text-decoration:none}

/* header */
.site-header{left:0;top:0;width:1200px;height:85px;background:var(--header)}
.brand{display:flex;align-items:center;gap:8px;font-weight:600;font-size:36px;letter-spacing:1px;color:var(--ink);line-height:1}
.brand-dot{width:30px;height:30px;border-radius:50%;background:var(--green)}
.site-header .brand{position:absolute;left:114px;top:25px}
.main-nav{position:absolute;left:353px;top:32px;display:flex;gap:26px;font-size:16px;color:var(--ink)}
.header-btn{left:920px;top:18px;width:167px;height:49px}

/* hero */
.hero{left:0;top:85px;width:1200px;height:514px;background:linear-gradient(120deg,#6b5a4a 0%,#4a3d33 40%,#7d6a58 70%,#a8a29a 100%)}
.hero-title{left:109px;top:210px;font-size:58px;font-weight:800;line-height:66px;color:var(--white)}
.hero-btn{left:108px;top:377px;width:141px;height:50px}

/* about */
.about-frame{left:106px;top:684px;width:426px;height:362px;background:var(--green)}
.about-photo{left:141px;top:713px;width:428px;height:362px;background:linear-gradient(120deg,#e8ddd2,#e68a4e 45%,#7b8a8f 80%,#c8c6c2)}
.section-title{font-size:38px;font-weight:700;color:var(--ink);display:flex;align-items:center;gap:14px;line-height:1}
.section-title .rule{display:block;width:40px;height:2px;background:var(--green)}
.about-title{left:599px;top:672px}
.about-lead{left:595px;top:736px;width:490px;font-size:22.5px;font-weight:500;line-height:35px;color:var(--ink)}
.about-body{left:595px;top:822px;width:485px;font-size:14.5px;line-height:25.8px}
.about-btn{left:597px;top:1061px;width:141px;height:49px}

/* services */
.services-title{left:0;width:1200px;top:1175px;justify-content:center}
.service{position:absolute;top:1284px;width:300px;height:334px;background:var(--green)}
.service-photo{width:300px;height:252px}
.service-name{text-align:center;color:var(--white);font-size:26px;font-weight:600;margin-top:13px}
.s1{left:108px}.s1 .service-photo{background:linear-gradient(135deg,#f1ede6,#d8c7b4 50%,#7c9bc2)}
.s2{left:447px}.s2 .service-photo{background:linear-gradient(135deg,#9aa3a8,#c9d3da 50%,#5b6167)}
.s3{left:786px}.s3 .service-photo{background:linear-gradient(135deg,#b79a7e,#e0a0a0 50%,#e8e6e2)}

/* courses */
.courses{left:0;top:1690px;width:1200px;height:486px;background:linear-gradient(90deg,#b7b9b0 0%,#3d7fd6 25%,#9cb0c4 50%,#c9cbc9 75%,#b44c3e 100%)}
.courses-circle{left:666px;top:1748px;width:376px;height:376px;border-radius:50%;background:var(--green);color:var(--white);text-align:center}
.courses-circle .section-title{color:var(--white);justify-content:center;margin-top:48px;font-size:40px}
.courses-circle .rule{background:var(--white)}
.courses-text{width:300px;margin:16px auto 0;font-size:15px;line-height:25.8px}
.courses-btn{left:117px;top:292px;width:141px;height:49px;background:var(--white);color:var(--green)}

/* testimonials */
.testi-title{left:0;width:1200px;top:2258px;justify-content:center}
.testi-wave{left:0;top:2440px;width:1200px;height:308px}
.testi-card{position:absolute;top:2331px;width:381px;height:349px;background:var(--cream);padding:24px 20px 0 21px}
.quote{font-size:90px;font-weight:800;color:var(--green);line-height:70px;height:56px}
.testi-text{font-size:15px;line-height:25.8px;color:var(--text);margin-top:6px}
.person{display:flex;align-items:center;gap:9px;margin-top:4px}
.avatar{width:68px;height:68px;border-radius:50%;background:linear-gradient(135deg,#d9c2ac,#6d84a4)}
.person-name{font-size:18px;font-weight:500;color:var(--ink);line-height:24px}
.person-role{font-size:16px;line-height:24px}
.t1{left:160px}.t2{left:653px}
.arrow{position:absolute;top:2502px;width:20px;height:20px}

/* footer */
.site-footer{left:0;top:2748px;width:1200px;height:279px;background:var(--footer);color:var(--white)}
.site-footer .brand{position:absolute;left:0;width:1200px;justify-content:center;top:50px;color:var(--white)}
.socials{position:absolute;left:0;width:1200px;top:120px;display:flex;justify-content:center;gap:15px}
.social{width:38px;height:38px;border-radius:50%;border:2px solid var(--white)}
.footer-nav{position:absolute;left:0;width:1200px;top:183px;display:flex;justify-content:center;gap:12px;font-size:16px}
.footer-rule{position:absolute;left:108px;top:231px;width:977px;height:1px;background:#cfcfcf}
.copyright{position:absolute;left:0;width:1200px;top:241px;text-align:center;font-size:15px}
.copyright span{color:var(--green)}
</style>
</head>
<body>

<header class="abs site-header">
  <div class="brand"><span>NOVAFIT</span><span class="brand-dot"></span></div>
  <nav class="main-nav"><span>ABOUT US</span><span>SERVICES</span><span>COURSES</span><span>TESTIMONIALS</span><span>CONTACT US</span></nav>
  <a class="btn header-btn">Get Appointment</a>
</header>

<section class="abs hero" role="img" aria-label="Trainer coaching a woman doing a lunge with suspension straps in a brick-walled gym"></section>
<h1 class="abs hero-title">WELCOME TO<br>NOVAFIT</h1>
<a class="btn hero-btn">Read More</a>

<div class="abs about-frame"></div>
<div class="abs about-photo" role="img" aria-label="Smiling woman on a rowing machine with her trainer beside her"></div>
<h2 class="abs section-title about-title">About Us <span class="rule"></span></h2>
<p class="abs about-lead">Lorem Ipsum is simply dummy text of the printing and typesetting industry. Lorem '</p>
<div class="abs about-body">
  <p>Lorem Ipsum is simply dummy text of the printing and typesetting industry. Lorem Ipsum has been the industry's standard dummy text ever since the 1500s, when an unknown printer took a galley of type and scrambled it to make a type specimen book.</p>
  <p>Lorem Ipsum is simply dummy text of the printing and typesetting industry. Lorem Ipsum has been the industry's standard dummy text ever since the 1500s, when an unknown printer took a galley of type and scrambled it to make a type specimen book</p>
</div>
<a class="btn about-btn">Read More</a>

<h2 class="abs section-title services-title"><span class="rule"></span>Services<span class="rule"></span></h2>
<div class="service s1"><div class="service-photo" role="img" aria-label="Nutritionist showing a meal plan to a client"></div><div class="service-name">Diet Coaching</div></div>
<div class="service s2"><div class="service-photo" role="img" aria-label="Trainer guiding an older woman through a floor exercise on a mat"></div><div class="service-name">In-Person Coaching</div></div>
<div class="service s3"><div class="service-photo" role="img" aria-label="Woman stretching on a mat at home in front of a laptop"></div><div class="service-name">Remote Coaching</div></div>

<section class="abs courses" role="img" aria-label="Smiling coach with a whistle in a gym with medicine balls"></section>
<div class="abs courses-circle">
  <h2 class="section-title"><span class="rule"></span>Courses<span class="rule"></span></h2>
  <p class="courses-text">Lorem Ipsum is simply dummy text of the printing and typesetting industry. Lorem Ipsum has been the industry's standard dummy text ever since the 1500s, when an unknown printer took a galley of type and scrambled it to make the printing and typesetting</p>
  <a class="btn courses-btn">Read More</a>
</div>

<h2 class="abs section-title testi-title"><span class="rule"></span>Testimonials<span class="rule"></span></h2>
<svg class="abs testi-wave" viewBox="0 0 1200 308" preserveAspectRatio="none">
  <path d="M0 40 C150 0 300 10 450 45 C600 80 650 20 800 25 C950 30 1050 -5 1200 20 L1200 308 L0 308 Z" fill="var(--green)"/>
</svg>
<svg class="arrow" style="left:59px" viewBox="0 0 20 20"><path d="M13 3 L6 10 L13 17" fill="none" stroke="#fff" stroke-width="2"/></svg>
<svg class="arrow" style="left:1106px" viewBox="0 0 20 20"><path d="M7 3 L14 10 L7 17" fill="none" stroke="#fff" stroke-width="2"/></svg>

<article class="testi-card t1">
  <div class="quote">“</div>
  <p class="testi-text">Lorem Ipsum is simply dummy text of<br>the printing and typesetting industry.<br>Lorem Ipsum has been the industry's<br>standard dummy text ever since the<br>1500s, when an unknown printer took a<br>galley of type and scrambled it to make<br>the printing and typesetting</p>
  <div class="person"><div class="avatar" role="img" aria-label="Client portrait"></div><div><div class="person-name">Halvorsen</div><div class="person-role">Client</div></div></div>
</article>
<article class="testi-card t2">
  <div class="quote">“</div>
  <p class="testi-text">Lorem Ipsum is simply dummy text of<br>the printing and typesetting industry.<br>Lorem Ipsum has been the industry's<br>standard dummy text ever since the<br>1500s, when an unknown printer took a<br>galley of type and scrambled it to make<br>the printing and typesetting</p>
  <div class="person"><div class="avatar" role="img" aria-label="Client portrait"></div><div><div class="person-name">daniel Frost</div><div class="person-role">Client</div></div></div>
</article>

<footer class="abs site-footer">
  <div class="brand"><span>NOVAFIT</span><span class="brand-dot"></span></div>
  <div class="socials"><span class="social"></span><span class="social"></span><span class="social"></span></div>
  <nav class="footer-nav"><span>ABOUT US</span><span>.</span><span>SERVICES</span><span>.</span><span>COURSES</span><span>.</span><span>TESTIMONIALS</span><span>.</span><span>CONTACT US</span></nav>
  <div class="footer-rule"></div>
  <p class="copyright"><span>©</span> 2023 Novafit | All Rights Reserved</p>
</footer>

</body>
</html>
```